Bring me business with this creative business card

Design my new business card. I am looking for something different with an impact. People will take a look at this card & they will 1- see how different & creative I am, 2-understand what I do 3- Call me to meet me!

I make videos with a message, testimonials. I am dynamic, fun, creative & human. My new website is in construction but in the meantime you can check this old one: brightpath.ca & another one Tidebloom.com & tidebloom facebook page.
I make videos. sometimes with a cameraman, sometimes with my phone. As an ex Public Relations agent, the message is the most important thing for me. I want to make my clients shine! When they start with me they often remind me of a lamb, when I finish coaching them they are powerful like LIONS! That's why I need a powerful business card!

Target Market(s)

Entrepreneurs, solo entrepreneurs, small & medium companies & start ups. People i will meet while networking. People that need videos on their website & social Networks to get attention, to be visible. men & women. From 35 to 49 years old.
I am an ex Public relations agent. I used to send clients in traditional medias, now with videos they have more chances to be seen on google the new media. I do videos of the president, his team, his loyal clients saying how great the company is & expert videos like series so people can be seen for example every 1 st of every month with a short 2 minute video. Also with my 20 years in marketing & communications I can coach & give tips to anybody who needs it.
Target: anybody who would like my old website brightpath.ca & I also have another website but it will be off line soon: tidebloom.com could give you ideas.

Industry/Entity Type

Communications

Contact Information for Business Card

I am in Montreal,So the business cards have to be the usual size like we have in Montreal: 9 cm x 5 cm
Details:My text: Mathilde Tessier Communication coach/Chief Storyteller. "Videos that let your message shine" off: 514-555-0147 cell: 514-555-0183. tidebloom.com
mathilde@tidebloom.com logo facebook, youtube, instagram

Colors
f37122

Requirements
Must have
• Dynamic, happy. Orange. Be creative in the look but NOT the shape of the card. Easy to read. Big enough to read.
Should not have
• No funny shapes: no round, no square, just the usual. I love creative but NOT on shape.

```html
<!DOCTYPE html>
<html lang="en">
<head>
<meta charset="utf-8">
<title>Tidebloom business card</title>
<link rel="stylesheet" href="https://fonts.googleapis.com/css2?family=Open+Sans:wght@400;600&display=swap">
<style>
  :root {
    --orange: #f37122;
    --orange-deep: #e8511f;
    --amber: #f7a21b;
    --ink: #3a3a3a;
    --paper: #ffffff;
    --night: #1e1f20;
    --backdrop: #ece8e3;
  }
  * { box-sizing: border-box; margin: 0; padding: 0; }
  html, body { width: 1200px; height: 911px; overflow: hidden; }
  body {
    background: var(--backdrop);
    font-family: "Open Sans", sans-serif;
    position: relative;
  }
  .card {
    position: absolute;
    width: 620px;
    height: 344px;
    border-radius: 4px;
    overflow: hidden;
    box-shadow: 0 6px 18px rgba(0,0,0,.18);
  }

  /* Front */
  .card--front { left: 80px; top: 80px; background: var(--paper); }
  .front__band {
    position: absolute; left: 0; top: 150px; bottom: 0; width: 96px;
    background: var(--orange);
  }
  .front__dot {
    position: absolute; left: 18px; top: 112px; width: 78px; height: 78px;
    border-radius: 50%; background: var(--amber); border: 4px solid var(--paper);
  }
  .front__glow {
    position: absolute; right: -30px; top: -20px; width: 330px; height: 300px;
    border-radius: 50%;
    background: radial-gradient(circle at 50% 50%, #fbe3c9 0%, #fdf0e3 60%, rgba(255,255,255,0) 75%);
  }
  .front__content { position: absolute; left: 130px; top: 40px; }
  .brand-name {
    font-family: "Open Sans", sans-serif; font-weight: 600; color: var(--orange-deep);
    font-size: 40px; letter-spacing: 3px; line-height: 1;
  }
  .person { margin-top: 40px; }
  .person__name { font-weight: 600; font-size: 20px; color: var(--orange-deep); letter-spacing: .5px; }
  .person__role { font-size: 15px; color: var(--amber); line-height: 1.3; }
  .contacts { list-style: none; margin-top: 14px; font-size: 14px; color: var(--ink); line-height: 1.55; }
  .contacts li { display: flex; align-items: center; gap: 8px; }
  .contacts svg { width: 12px; height: 12px; fill: var(--orange-deep); }

  /* Back */
  .card--back { left: 500px; top: 490px; background: var(--night); }
  .back__lockup { position: absolute; left: 70px; top: 104px; display: flex; align-items: center; gap: 40px; }
  .back__dot { width: 110px; height: 110px; border-radius: 50%; background: var(--amber); }
  .back__name { font-family: "Open Sans", sans-serif; font-weight: 600; color: var(--orange); font-size: 42px; letter-spacing: 3px; line-height: 1; }
  .back__slogan { font-size: 15px; color: var(--orange); margin-top: 14px; }
  .back__footer {
    position: absolute; left: 0; right: 0; bottom: 38px;
    display: flex; justify-content: center;
  }
  .back__footer .rule { height: 1px; width: 400px; background: var(--orange); }
</style>
</head>
<body>

<section class="card card--front" aria-label="Business card front">
  <div class="front__glow" role="img" aria-label="Soft orange glow where a faint brand emblem sits"></div>
  <div class="front__band"></div>
  <div class="front__dot"></div>
  <div class="front__content">
    <div class="brand-name">TIDEBLOOM</div>
    <div class="person">
      <div class="person__name">MATHILDE T.</div>
      <div class="person__role">COMMUNICATION COACH</div>
      <div class="person__role">CHIEF STORYTELLER</div>
    </div>
    <ul class="contacts">
      <li><svg viewBox="0 0 12 12"><path d="M2 1h3l1 3-2 1a7 7 0 0 0 3 3l1-2 3 1v3c-6 1-10-4-9-9z"/></svg>514-555-0147</li>
      <li><svg viewBox="0 0 12 12"><rect x="3" y="0" width="6" height="12" rx="1"/></svg>514-555-0183</li>
      <li><svg viewBox="0 0 12 12"><path d="M0 2h12v8H0z"/></svg>mathilde@tidebloom.com</li>
      <li><svg viewBox="0 0 12 12"><circle cx="6" cy="6" r="6"/></svg>www.tidebloom.com</li>
    </ul>
  </div>
</section>

<section class="card card--back" aria-label="Business card back">
  <div class="back__lockup">
    <div>
      <div class="back__name">TIDEBLOOM</div>
      <div class="back__slogan">Videos that let your message shine</div>
    </div>
    <div class="back__dot"></div>
  </div>
  <div class="back__footer">
    <span class="rule"></span>
  </div>
</section>

</body>
</html>
```